RevelHubQZ Business Cards

Front
Has logo with a design. Website address (www.revelhubqz-example.net)
Has slogan (discover the nightlife)
Has phone number (5182297734)
Should be bold and stands out.

Back
Has details about what we offer.

Events
Search upcoming events
Submit events
Party Image Gallery
View and download HQ party images
Sign up as a contributing event photographer and get paid!
Tickets
Sell your event tickets online for free!
Direct pay
No ticket fee

Target Market(s)

These cards will be handed out in clubs and events to patrons.

Industry/Entity Type

Business

Contact Information for Business Card

Should match or mirror our website in some sort of way. Visit the website to get ideas.

Requirements
Must have
• Must be designed for a 3x3 inch card.

```html
<!DOCTYPE html>
<html lang="en">
<head>
<meta charset="utf-8">
<title>RevelHubQZ Business Cards</title>
<link href="https://fonts.googleapis.com/css2?family=Exo+2:wght@300;400;500;600&display=swap" rel="stylesheet">
<style>
  :root {
    --stage: #1f1f21;
    --card: #ffffff;
    --blue: #3aa7dd;
    --pink: #e6469b;
    --ink-soft: #4a4a4a;
    --card-size: 460px;
  }
  * { box-sizing: border-box; margin: 0; padding: 0; }
  html, body {
    width: 1200px;
    height: 950px;
    overflow: hidden;
    background: var(--stage);
    font-family: "Exo 2", sans-serif;
  }
  .sheet {
    width: 1200px;
    height: 950px;
    display: flex;
    align-items: center;
    justify-content: center;
    gap: 60px;
  }
  .card {
    position: relative;
    width: var(--card-size);
    height: var(--card-size);
    background: var(--card);
    border-radius: 4px;
    overflow: hidden;
    box-shadow: 0 12px 30px rgba(0,0,0,0.45);
  }
  .equalizer-band {
    position: absolute;
    left: 0;
    right: 0;
    bottom: 0;
    height: 92px;
    background: linear-gradient(to top, var(--blue) 0%, rgba(58,167,221,0.85) 35%, rgba(230,70,155,0.75) 70%, rgba(230,70,155,0) 100%);
  }

  /* Front */
  .card-front .brand {
    position: absolute;
    top: 96px;
    left: 0;
    right: 0;
    text-align: center;
  }
  .brand-row {
    display: inline-flex;
    align-items: center;
    gap: 12px;
  }
  .brand-dot {
    width: 26px;
    height: 26px;
    border-radius: 50%;
    background: var(--blue);
  }
  .brand-name {
    font-size: 48px;
    font-weight: 500;
    color: var(--blue);
    letter-spacing: 0.5px;
    line-height: 1.1;
  }
  .slogan {
    margin-top: 4px;
    font-size: 14px;
    font-weight: 400;
    letter-spacing: 3px;
    color: var(--blue);
  }
  .contact {
    position: absolute;
    top: 210px;
    left: 0;
    right: 0;
    text-align: center;
  }
  .phone-icon { width: 30px; height: 30px; display: block; margin: 0 auto 8px; }
  .phone-number {
    font-size: 44px;
    font-weight: 600;
    color: var(--blue);
    letter-spacing: 1px;
    line-height: 1.15;
  }
  .website {
    margin-top: 8px;
    font-size: 16px;
    font-weight: 500;
    color: var(--pink);
    letter-spacing: 0.5px;
  }

  /* Back */
  .card-back .section-mark {
    position: absolute;
    top: 54px;
    left: 50%;
    width: 48px;
    height: 48px;
    margin-left: -24px;
    border-radius: 50%;
    background: var(--blue);
  }
  .section-title {
    position: absolute;
    top: 108px;
    left: 0;
    right: 0;
    text-align: center;
    font-size: 30px;
    font-weight: 600;
    color: var(--blue);
  }
  .offer-list {
    position: absolute;
    top: 158px;
    left: 0;
    right: 0;
    list-style: none;
    text-align: center;
    font-size: 18px;
    font-weight: 400;
    line-height: 1.55;
    color: var(--ink-soft);
  }
  .offer-list .sep { color: var(--blue); font-weight: 600; }
</style>
</head>
<body>
<main class="sheet">
  <section class="card card-front">
    <div class="brand">
      <div class="brand-row">
        <span class="brand-dot"></span>
        <span class="brand-name">RevelHubQZ</span>
      </div>
      <p class="slogan">discover the nightlife</p>
    </div>
    <div class="contact">
      <svg class="phone-icon" viewBox="0 0 30 30" aria-hidden="true">
        <circle cx="15" cy="15" r="13" fill="none" stroke="#e6469b" stroke-width="2"/>
        <path d="M10.5 9c1-.8 2-.6 2.4.3l1 2c.3.6.1 1.2-.4 1.6l-.8.6c.6 1.5 1.7 2.7 3.2 3.4l.6-.8c.4-.5 1-.7 1.6-.4l2 1c.9.4 1.1 1.4.3 2.4-1 1.2-2.6 1.4-4.2.6-2.9-1.4-5-3.6-6.3-6.4-.8-1.7-.5-3.3.6-4.3z" fill="#e6469b"/>
      </svg>
      <p class="phone-number">5182297734</p>
      <p class="website">www.revelhubqz-example.net</p>
    </div>
    <div class="equalizer-band" role="img" aria-label="Equalizer pattern of pink and blue squares"></div>
  </section>

  <section class="card card-back">
    <span class="section-mark"></span>
    <h2 class="section-title">Events</h2>
    <ul class="offer-list">
      <li>Sell your event tickets online for free!</li>
      <li>View &amp; download HQ party images</li>
      <li>Sign up as a contributing event</li>
      <li>photographer &amp; get paid! <span class="sep">•</span> Tickets</li>
      <li>Submit events <span class="sep">•</span> Direct pay</li>
      <li>Party Image Gallery <span class="sep">•</span> No ticket fee</li>
      <li>Search upcoming events</li>
    </ul>
    <div class="equalizer-band" role="img" aria-label="Equalizer pattern of pink and blue squares"></div>
  </section>
</main>
</body>
</html>
```